TA BRAMLEY BUSINESS CARD DESIGN PROJECT

We need to utilize our logo that was expertly created on PixelHarbor and now need to match this with a business card design.

```html
<!DOCTYPE html>
<html lang="en">
<head>
<meta charset="utf-8">
<title>TA Bramley Business Card</title>
<link rel="stylesheet" href="https://fonts.googleapis.com/css2?family=Montserrat:wght@400;500;700;800&display=swap">
<style>
  :root {
    --bg: #d6d6d6;
    --paper: #f1f1f1;
    --brand-blue: #0d3fa6;
    --ink: #1b1b1b;
  }
  * { box-sizing: border-box; margin: 0; padding: 0; }
  html, body {
    width: 1200px; height: 1051px; overflow: hidden;
    background: var(--bg);
    font-family: "Montserrat", sans-serif;
  }
  .canvas {
    position: relative; width: 1200px; height: 1051px;
  }
  .card {
    position: absolute; left: 250px;
    width: 700px; height: 400px;
    background: var(--paper);
    overflow: hidden;
    border-bottom: 6px solid var(--brand-blue);
    box-shadow: 0 14px 30px rgba(0,0,0,0.18);
  }
  .card--contact { top: 90px; }
  .card--brand { top: 560px; display: flex; align-items: center; justify-content: center; }

  .wordmark {
    color: var(--brand-blue);
    font-weight: 800;
    letter-spacing: 0.18em;
    line-height: 1;
    white-space: nowrap;
  }
  .wordmark--small { position: absolute; left: 48px; top: 52px; font-size: 30px; }
  .wordmark--large { font-size: 70px; }

  .holder {
    position: absolute; right: 48px; top: 56px; text-align: right;
  }
  .holder__name {
    color: var(--brand-blue); font-weight: 700; font-size: 20px; letter-spacing: 0.02em;
  }
  .holder__role {
    color: var(--ink); font-weight: 400; font-size: 15px; margin-top: 4px;
  }

  .address {
    position: absolute; left: 48px; top: 170px;
    color: var(--ink); font-size: 15px; line-height: 1.35;
  }
  .contacts {
    position: absolute; left: 48px; top: 236px; list-style: none;
    color: var(--ink); font-size: 15px; line-height: 1.6;
  }
  .contacts li { display: flex; align-items: center; gap: 8px; }
  .contacts svg { width: 13px; height: 13px; fill: var(--brand-blue); flex: none; }

  .decor-mark {
    position: absolute; right: -40px; bottom: -22px;
    color: var(--brand-blue); font-weight: 800; font-size: 120px;
    letter-spacing: 0.05em; line-height: 1; white-space: nowrap;
  }
</style>
</head>
<body>
<main class="canvas">
  <section class="card card--contact">
    <div class="wordmark wordmark--small">TA BRAMLEY</div>

    <div class="holder">
      <div class="holder__name">COLIN ASHBY</div>
      <div class="holder__role">Managing Director</div>
    </div>

    <p class="address">Your address, City<br>State, Zip 1234</p>

    <ul class="contacts">
      <li>
        <svg viewBox="0 0 16 16" aria-hidden="true"><path d="M3 1h3l1.5 4-2 1.5a9 9 0 0 0 4 4L11 8.5l4 1.5v3a2 2 0 0 1-2 2A12 12 0 0 1 1 3a2 2 0 0 1 2-2z"/></svg>
        123 456 789
      </li>
      <li>
        <svg viewBox="0 0 16 16" aria-hidden="true"><path d="M1 3h14v10H1z M1 3l7 6 7-6" stroke="#f1f1f1" stroke-width="1.2"/></svg>
        info@yourmail.com
      </li>
      <li>
        <svg viewBox="0 0 16 16" aria-hidden="true"><circle cx="8" cy="8" r="7"/></svg>
        www.yourwebsite.com
      </li>
    </ul>

    <div class="decor-mark" aria-hidden="true">TA BRAMLEY</div>
  </section>

  <section class="card card--brand">
    <div class="wordmark wordmark--large">TA BRAMLEY</div>
  </section>
</main>
</body>
</html>
```